Indy Film Production Company/Studio

We need a business card designed from an existing logo. We are a digital studio/production company that caters to creating genre entertainment, like Action, Horror, and martial arts. The card along with the logo will be used to Brand the company from letter heads to banners. The design will also be used for postcards and Brochures. It should be professional and masculine.
Updates

Thank you to all the designers who have participated. I'm narrowing down who it will be. Thank you again.

Target Market(s)

Investors, Networks, Producers, and actors

Industry/Entity Type

Film Production

Contact Information for Business Card

Teodoro Valbuena
Producer/Writer/Director
www.kestrelpicturehouse.example

Requirements
Must have
• Website address, Facebook icon and Twitter icon possibly in the back of the card.
Nice to have
• Logline of Company: Follow The Action.

```html
<!DOCTYPE html>
<html lang="en">
<head>
<meta charset="utf-8">
<title>Kestrel Picture House – Business Card</title>
<link rel="stylesheet" href="https://fonts.googleapis.com/css2?family=Source+Sans+3:wght@400;600;700&display=swap">
<style>
  :root {
    --backdrop: #e9e6e1;
    --kraft: #c4a47c;
    --kraft-light: #cdae86;
    --ink: #161310;
    --card-shadow: rgba(0, 0, 0, 0.18);
  }
  html, body {
    margin: 0;
    padding: 0;
    width: 1200px;
    height: 900px;
    overflow: hidden;
    background: var(--backdrop);
  }
  .canvas {
    position: relative;
    width: 1200px;
    height: 900px;
    font-family: "Source Sans 3", "Myriad Pro", Arial, sans-serif;
    color: var(--ink);
  }
  .card {
    position: absolute;
    background: linear-gradient(135deg, var(--kraft-light), var(--kraft));
    box-shadow: 0 6px 18px var(--card-shadow);
    box-sizing: border-box;
  }
  .card--front {
    left: 78px;
    top: 35px;
    width: 587px;
    height: 363px;
    text-align: center;
  }
  .card--back {
    left: 388px;
    top: 505px;
    width: 567px;
    height: 352px;
  }
  .holder-name {
    position: absolute;
    top: 67px;
    left: 0;
    right: 0;
    margin: 0;
    font-size: 20px;
    line-height: 26px;
    font-weight: 600;
    letter-spacing: 0.2px;
  }
  .holder-title {
    position: absolute;
    top: 97px;
    left: 0;
    right: 0;
    margin: 0;
    font-size: 16px;
    line-height: 20px;
    font-weight: 400;
  }
  .contact-list {
    position: absolute;
    top: 170px;
    left: 0;
    right: 0;
    margin: 0;
    padding: 0;
    list-style: none;
    font-size: 16px;
    line-height: 20px;
  }
  .address {
    position: absolute;
    top: 289px;
    left: 0;
    right: 0;
    margin: 0;
    font-size: 16px;
    line-height: 20px;
  }
  .brand-name {
    position: absolute;
    left: 0;
    right: 0;
    top: 152px;
    margin: 0;
    text-align: center;
    font-size: 32px;
    line-height: 40px;
    font-weight: 700;
    letter-spacing: 1px;
    text-transform: uppercase;
    color: var(--ink);
  }
</style>
</head>
<body>
<main class="canvas">
  <section class="card card--front" aria-label="Business card front">
    <h1 class="holder-name">TEODORO VALBUENA</h1>
    <p class="holder-title">Producer/Writer/Director</p>
    <ul class="contact-list">
      <li>044-555-0184</li>
      <li>123-555-0142</li>
      <li>info@kestrelpicturehouse.example</li>
      <li>www.kestrelpicturehouse.example</li>
    </ul>
    <p class="address">88 Foundry Lane | Northvale, AB | 204517</p>
  </section>

  <section class="card card--back" aria-label="Business card back">
    <p class="brand-name">Kestrel Picture House</p>
  </section>
</main>
</body>
</html>
```